Business Cards for new orthopaedic surgery practice

My husband and I are starting our own orthopaedic surgery practice. We are looking for a business card that is uniform, but one will have my name/title and the other will have his. You can just create one design with my name on it for now. But when I choose your design as the winning design I will ask that you add another copy with his name/title.

We are looking for classy, simple, elite all in one. We like dark blues/a little gold/yellow. Something that goes with our logo. We want our logo incorporated. Here is all the info you need:
Business name: RV Bone & Vitality Center
Location: 38517 North Willowmere Ave
Coral Springs, FL 33071
Phone: 954-218-4063
Fax: 954-582-7341
Email: info@myrvbonecare.example

Names: Lydia Vance, M.D.
Board Certified Hand and Upper Extremity Surgeon

Ebo Dansu, M.D.
Board Certified Hip & Knee Replacement/General Orthopaedic Surgeon

Can decide what you want to put on the back. Maybe a slogan:
Rooted in Care. Focused on You

I am just going to upload our logo. The only thing is if we select you as the winning design, the location, and phone numbers may change. We will need your help to update that once fully solidified.

Industry/Entity Type

Medical

Contact Information for Business Card

Colors
0054AA
0677BA
7BADD7
CADEEF
E8F1F8
0094D4
00A9DD
6FCCEA
C7EBF8
E9F6FB

Requirements
Must have
• class, appeal,
Should not have
• We want to air on the side of masculine if we are looking at masculine vs. feminine feel. But we still want it classy, sophisticated, and something we will love

```html
<!DOCTYPE html>
<html lang="en">
<head>
<meta charset="utf-8">
<title>RV Bone &amp; Vitality Center — Business Card</title>
<link rel="stylesheet" href="https://fonts.googleapis.com/css2?family=Poppins:wght@400;500;600&display=swap">
<style>
  :root {
    --page-bg: #1b1b1e;
    --card-navy: #253b8c;
    --card-navy-deep: #1f3280;
    --pattern-light: #3550a8;
    --accent-cyan: #1fb6e6;
    --ink-white: #ffffff;
  }
  * { box-sizing: border-box; margin: 0; padding: 0; }
  html, body {
    width: 1200px; height: 900px; overflow: hidden;
    background: var(--page-bg);
    font-family: "Poppins", sans-serif;
  }
  .canvas {
    width: 1200px; height: 900px;
    display: flex; flex-direction: column; align-items: center; justify-content: center;
    gap: 40px;
  }
  .card {
    position: relative;
    width: 700px; height: 400px;
    background: var(--card-navy);
    overflow: hidden;
    box-shadow: 0 10px 30px rgba(0,0,0,.5);
  }
  /* Front */
  .card-front__decoration {
    position: absolute; left: 0; top: 0;
    width: 380px; height: 400px;
    background: radial-gradient(ellipse at 45% 35%, rgba(255,255,255,.07), rgba(255,255,255,0) 70%);
  }
  .brand-lockup {
    position: absolute;
    display: flex; align-items: center; gap: 14px;
  }
  .brand-lockup__mark {
    width: 26px; height: 26px; border-radius: 50%;
    background: var(--ink-white); flex: none;
  }
  .brand-lockup__name {
    color: var(--ink-white);
    font-weight: 500;
    font-size: 22px; line-height: 1.25;
    width: 170px;
  }
  .card-front .brand-lockup { left: 60px; top: 150px; }
  .card-front__divider {
    position: absolute; left: 340px; top: 80px;
    width: 1.5px; height: 240px;
    background: var(--accent-cyan);
  }
  .contact {
    position: absolute; left: 372px; top: 96px;
    color: var(--ink-white);
  }
  .contact__name {
    color: var(--accent-cyan);
    font-weight: 600; font-size: 21px;
  }
  .contact__title { font-size: 14px; margin-top: 2px; }
  .contact__address { font-size: 14px; line-height: 1.45; margin-top: 18px; }
  .contact__list { list-style: none; margin-top: 16px; font-size: 14px; line-height: 1.7; }
  .contact__list li { display: flex; align-items: center; gap: 8px; }
  .contact__icon { width: 13px; height: 13px; fill: var(--accent-cyan); flex: none; }
  /* Back */
  .card-back__pattern {
    position: absolute; inset: 0;
    background: linear-gradient(135deg, var(--card-navy-deep), var(--pattern-light) 55%, var(--card-navy-deep));
  }
  .card-back .brand-lockup { right: 60px; bottom: 60px; }
  .card-back__divider {
    width: 1.5px; height: 70px; background: var(--ink-white); flex: none;
  }
</style>
</head>
<body>
<main class="canvas">
  <section class="card card-front" aria-label="Business card front">
    <div class="card-front__decoration" role="img" aria-label="Faint large tree emblem decoration"></div>
    <div class="brand-lockup">
      <span class="brand-lockup__mark"></span>
      <span class="brand-lockup__name">RV Bone &amp; Vitality Center</span>
    </div>
    <div class="card-front__divider"></div>
    <div class="contact">
      <p class="contact__name">Lydia Vance, M.D.</p>
      <p class="contact__title">Hand and Upper Extremity Surgery</p>
      <p class="contact__address">38517 North Willowmere Ave<br>Coral Springs, FL 33071</p>
      <ul class="contact__list">
        <li>
          <svg class="contact__icon" viewBox="0 0 24 24"><path d="M6.6 10.8a15 15 0 0 0 6.6 6.6l2.2-2.2a1 1 0 0 1 1-.25 11.4 11.4 0 0 0 3.6.57 1 1 0 0 1 1 1V20a1 1 0 0 1-1 1A17 17 0 0 1 3 4a1 1 0 0 1 1-1h3.5a1 1 0 0 1 1 1c0 1.25.2 2.45.57 3.57a1 1 0 0 1-.25 1z"/></svg>
          954-218-4063
        </li>
        <li>
          <svg class="contact__icon" viewBox="0 0 24 24"><path d="M6 3h9v5H6zM4 9h16a2 2 0 0 1 2 2v7H2v-7a2 2 0 0 1 2-2zm3 6v4h10v-4z"/></svg>
          954-582-7341
        </li>
        <li>
          <svg class="contact__icon" viewBox="0 0 24 24"><path d="M3 5h18v14H3zm2 2v.5l7 4.5 7-4.5V7z"/></svg>
          info@myrvbonecare.example
        </li>
      </ul>
    </div>
  </section>

  <section class="card card-back" aria-label="Business card back">
    <div class="card-back__pattern" role="img" aria-label="Repeating embossed emblem pattern in tonal blues"></div>
    <div class="brand-lockup">
      <span class="brand-lockup__mark"></span>
      <span class="card-back__divider"></span>
      <span class="brand-lockup__name">RV Bone &amp; Vitality Center</span>
    </div>
  </section>
</main>
</body>
</html>
```